design a construction company business card

Design business card around our logo. Card must have all the typical info: name, title, address, phone, email, business name, etc. Somewhere on the card I would like to see our motto "Built on integrity... Inspired by commitment." Consider adding a splash of bright orange to the card to complement the blues and silvers/grays in the logo. We are open to metallic inks, textures, etc. We would like to see options on both light and dark backgrounds. The font in the logo is Euro Technic Extended Regular.

```html
<!DOCTYPE html>
<html lang="en">
<head>
<meta charset="UTF-8">
<title>Harlow Contracting – Business Card</title>
<link href="https://fonts.googleapis.com/css2?family=Roboto:ital,wght@0,300;0,400;0,700;1,700&display=swap" rel="stylesheet">
<style>
  :root {
    --backdrop: #a7aeaf;
    --card: #f3f3f0;
    --navy: #1c2a8c;
    --navy-deep: #141c5e;
    --steel: #6b6e73;
    --ink: #1d1d1f;
  }
  * { box-sizing: border-box; margin: 0; padding: 0; }
  html, body {
    width: 1200px; height: 824px; overflow: hidden;
    background: var(--backdrop);
    font-family: "Roboto", Arial, sans-serif;
  }
  .stage {
    width: 1200px; height: 824px;
    display: flex; align-items: center; justify-content: center; gap: 40px;
  }
  .card {
    width: 540px; height: 309px;
    background: var(--card);
    position: relative;
    box-shadow: 0 8px 18px rgba(0,0,0,0.18);
  }
  .rule { position: absolute; height: 2px; background: var(--navy); }
  .rule--top { left: 70px; right: 150px; top: 48px; }
  .rule--mid { left: 60px; right: 70px; top: 146px; }
  .rule--bottom { left: 150px; right: 60px; top: 268px; }
  .identity {
    position: absolute; top: 62px; left: 0; right: 0; text-align: center;
  }
  .identity__mark {
    display: inline-block; width: 18px; height: 18px; background: var(--navy);
  }
  .identity__name {
    font-weight: 700; font-size: 21px; color: var(--navy); letter-spacing: 0.5px;
    margin-top: 4px;
  }
  .identity__title {
    font-weight: 400; font-size: 15px; color: var(--steel); letter-spacing: 0.5px;
  }
  .details {
    position: absolute; top: 162px; left: 0; right: 0; text-align: center;
    font-weight: 300; font-size: 14px; color: var(--ink); line-height: 22px;
  }
  .motto {
    position: absolute; top: 234px; left: 0; right: 0; text-align: center;
    font-weight: 700; font-style: italic; font-size: 14px; color: var(--ink);
  }
  .card--brand {
    display: flex; align-items: center; justify-content: center;
    border-bottom: 6px solid var(--navy-deep);
  }
  .brand { display: flex; align-items: center; gap: 14px; }
  .brand__square { width: 26px; height: 26px; background: var(--navy); }
  .brand__name {
    font-weight: 700; font-size: 30px; color: var(--navy); letter-spacing: 1px;
  }
</style>
</head>
<body>
  <main class="stage">
    <section class="card card--contact" aria-label="Business card, contact side">
      <div class="rule rule--top"></div>
      <div class="identity">
        <span class="identity__mark"></span>
        <p class="identity__name">DANIEL REEVE</p>
        <p class="identity__title">CEO/FOUNDER</p>
      </div>
      <div class="rule rule--mid"></div>
      <div class="details">
        <p>4120 Birchwood Road, Anchorage, Alaska 99517</p>
        <p>907 555 0142 &nbsp;|&nbsp; daniel@harlowbuild.com &nbsp;|&nbsp; www.harlowbuild.com</p>
      </div>
      <p class="motto">Grounded in trust...Driven by dedication.</p>
      <div class="rule rule--bottom"></div>
    </section>
    <section class="card card--brand" aria-label="Business card, brand side">
      <div class="brand">
        <span class="brand__square"></span>
        <span class="brand__name">HARLOW CONTRACTING, INC.</span>
      </div>
    </section>
  </main>
</body>
</html>
```